Business card for Sports Apparel business

DOUBLE SIDED DESIGN
We need business cards for a new sports apparel business. We are developing a protective headband for soccer initially.
Torvalle is focused on designing and developing head protection products to reduce the likelihood of concussion when playing sports. Exploring and understanding medical insights, material science research, current and former players experiences and governing bodies guidelines has allowed Torvalle to develop the safety, style, form and function requirements of a suitable product to bring to market.
Target Market(s)
Mums buying kits for the sons and daughters. Amateur footballers.
Industry/Entity Type
Sporting Good
Contact Information for Business Card
Martin Ashworth - CEO
Mobile: +44 7431589027
Email: martin@torvalle.co.uk
Tel: 0208 5519372
Helena Pargeter - COO
Mob: +44 7385 640117
Email: helena@torvalle.co.uk
Tel: 0208 5519372
Duncan Farrow - CCO
Mob: +44 7564 293081
Email: duncan@torvalle.co.uk
Tel: 0208 5519372
Look and feel
Each slider illustrates characteristics of the customer's brand and the style your logo design should communicate.

```html
<!DOCTYPE html>
<html lang="en">
<head>
<meta charset="utf-8">
<title>Torvalle Business Card</title>
<link rel="stylesheet" href="https://fonts.googleapis.com/css2?family=Roboto:wght@400;500;700&display=swap">
<style>
  :root {
    --page-bg: #e6e7e9;
    --card-white: #ffffff;
    --brand-blue: #2e5f8a;
    --brand-blue-light: #3a78a8;
    --brand-blue-soft: #4a6f9e;
    --slate: #36495a;
    --charcoal: #26292c;
    --logo-grey: #5b5f63;
    --text-light: #ffffff;
  }
  * { box-sizing: border-box; margin: 0; padding: 0; }
  html, body {
    width: 1200px; height: 800px; overflow: hidden;
    background: var(--page-bg);
    font-family: "Roboto", Arial, sans-serif;
  }
  .canvas {
    width: 1200px; height: 800px;
    display: flex; align-items: center; justify-content: center; gap: 40px;
  }
  .card {
    position: relative;
    width: 540px; height: 309px;
    background: var(--card-white);
    border-radius: 4px;
    overflow: hidden;
    box-shadow: 0 10px 28px rgba(0,0,0,0.18);
  }
  .card-art { position: absolute; inset: 0; }
  .wordmark {
    position: absolute;
    display: flex; align-items: center; gap: 10px;
  }
  .wordmark-square {
    width: 14px; height: 14px; background: var(--brand-blue-light);
  }
  .wordmark-name {
    font-weight: 500; font-size: 28px; letter-spacing: 2px;
    color: var(--logo-grey); text-transform: uppercase;
  }
  .card-front .wordmark { left: 70px; top: 152px; }
  .card-back .wordmark { left: 34px; top: 52px; }
  .card-back .wordmark-name { font-size: 24px; }

  .person {
    position: absolute; right: 34px; top: 40px;
    text-align: right; color: var(--text-light);
  }
  .person-name { font-weight: 700; font-size: 17px; text-transform: uppercase; letter-spacing: 0.3px; }
  .person-title { font-size: 12.5px; margin-top: 4px; }
  .person-rule { width: 150px; height: 1.5px; background: var(--text-light); margin: 8px 0 0 auto; }

  .contact-list {
    position: absolute; left: 352px; top: 198px;
    list-style: none; color: var(--text-light); font-size: 13px;
  }
  .contact-item { display: flex; align-items: center; gap: 9px; margin-bottom: 11px; white-space: nowrap; }
  .contact-icon { width: 16px; height: 16px; flex: none; }
</style>
</head>
<body>
<main class="canvas">

  <section class="card card-front" aria-label="Card front">
    <svg class="card-art" viewBox="0 0 540 309" width="540" height="309" aria-hidden="true">
      <polygon points="335,0 540,0 540,309 425,309 335,170" fill="var(--brand-blue)"/>
      <polygon points="335,170 420,125 420,309 425,309" fill="var(--brand-blue-light)"/>
      <polygon points="420,125 540,125 540,309 420,309" fill="var(--slate)"/>
      <polygon points="335,170 425,309 390,309 335,215" fill="var(--card-white)"/>
    </svg>
    <div class="wordmark">
      <span class="wordmark-square"></span>
      <span class="wordmark-name">Torvalle</span>
    </div>
  </section>

  <section class="card card-back" aria-label="Card back">
    <svg class="card-art" viewBox="0 0 540 309" width="540" height="309" aria-hidden="true">
      <polygon points="250,0 540,0 540,135 370,135 300,309 250,309" fill="var(--brand-blue)"/>
      <polygon points="250,0 300,0 300,309 250,309" fill="var(--brand-blue-soft)"/>
      <polygon points="250,240 300,210 300,309 250,309" fill="var(--brand-blue-light)"/>
      <polygon points="370,135 540,135 540,309 300,309" fill="var(--charcoal)"/>
      <polygon points="250,255 290,309 250,309" fill="var(--card-white)"/>
    </svg>
    <div class="wordmark">
      <span class="wordmark-square"></span>
      <span class="wordmark-name">Torvalle</span>
    </div>
    <div class="person">
      <p class="person-name">Martin Ashworth</p>
      <p class="person-title">Chief Executive Officer</p>
      <div class="person-rule"></div>
    </div>
    <ul class="contact-list">
      <li class="contact-item">
        <svg class="contact-icon" viewBox="0 0 16 16" aria-hidden="true"><circle cx="8" cy="8" r="8" fill="#fff"/><rect x="5.5" y="3.5" width="5" height="9" rx="1" fill="none" stroke="#26292c" stroke-width="1.2"/></svg>
        <span>+44 7431589027</span>
      </li>
      <li class="contact-item">
        <svg class="contact-icon" viewBox="0 0 16 16" aria-hidden="true"><circle cx="8" cy="8" r="8" fill="#fff"/><rect x="4" y="5" width="8" height="6" fill="none" stroke="#26292c" stroke-width="1.2"/><polyline points="4,5 8,8.5 12,5" fill="none" stroke="#26292c" stroke-width="1.2"/></svg>
        <span>martin@torvalle.co.uk</span>
      </li>
      <li class="contact-item">
        <svg class="contact-icon" viewBox="0 0 16 16" aria-hidden="true"><circle cx="8" cy="8" r="8" fill="#fff"/><path d="M5 4.5 L6.6 4.2 L7.3 6.3 L6.3 7 Q7.2 8.9 9 9.7 L9.7 8.7 L11.8 9.4 L11.5 11 Q8 11.5 5.8 9 Q4.3 7 5 4.5 Z" fill="#26292c"/></svg>
        <span>0208 5519372</span>
      </li>
    </ul>
  </section>

</main>
</body>
</html>
```